BrivoTerna. Lantern of the Steady Harvest. Business card

Professional business card for BrivoTerna (Lantern of the Steady Harvest)
My rationale: Strategy-> Execution-> Results-> Value that lead to the BrivoTerna name: We put the Lantern of the Steady Harvest.
We deliver value to our customers helping them at defining a good strategy (cyan arrow). 90% of well formulated strategies fail due to poor execution so we also consider strategical execution very important (green arrow). Due to the execution we obtain the results (blue arrow). Finally, the results provide feedback to redefine strategy, and the new strategy has to be executed and new results obtained providing new feedback and on and on. It's like a wheel that finally, must create corporate value: value for shareholders, staholders, employees, providers...-

Target Market(s)

CEOs and steering comitees , invewrnent funds

Industry/Entity Type

Business Consultant

Contact Information for Business Card

Teodoro Vinsquel
CEO & Founder
teodoro.vinsquel@brivoterna-example.com
Mobile: +34 655.803.912
www.brivoterna-example.com

Colors

Designer to choose colors to be used in the design.

Requirements
Nice to have
• Nice to hace the words: Strategy, execution, results
• Nice to vave the claim: Lantern of the Steady Harvest
• The three colors should be shown:
• cyan for STRATEGY
• green for EXECUTION
• blue for RESULTS
Should not have
• Complete black background

```html
<!DOCTYPE html>
<html lang="en">
<head>
<meta charset="utf-8">
<title>BrivoTerna – Business Card</title>
<link href="https://fonts.googleapis.com/css2?family=Roboto:wght@300;400;700&display=swap" rel="stylesheet">
<style>
  :root {
    --brand-blue: #0a3399;
    --brand-green: #8cc63f;
    --brand-cyan: #00b0eb;
    --card-white: #ffffff;
    --stage: #e9ebef;
  }
  html, body {
    margin: 0;
    padding: 0;
    width: 1200px;
    height: 880px;
    overflow: hidden;
    background: var(--stage);
    font-family: "Roboto", sans-serif;
  }
  .canvas {
    position: relative;
    width: 1200px;
    height: 880px;
  }
  .card {
    position: absolute;
    width: 600px;
    height: 345px;
    border-radius: 18px;
    overflow: hidden;
    box-shadow: 0 10px 30px rgba(10, 30, 80, 0.18);
  }
  .card--back {
    left: 60px;
    top: 90px;
    background: var(--brand-blue);
    display: flex;
    align-items: center;
    justify-content: center;
  }
  .card--front {
    left: 540px;
    top: 445px;
    background: var(--card-white);
  }
  .brand-name {
    display: flex;
    align-items: center;
    gap: 12px;
    font-weight: 700;
    letter-spacing: -0.5px;
  }
  .brand-name__dot {
    width: 16px;
    height: 16px;
    border-radius: 50%;
  }
  .card--back .brand-name {
    color: var(--card-white);
    font-size: 44px;
  }
  .card--back .brand-name__dot { background: var(--brand-green); }

  .front-wave {
    position: absolute;
    inset: 0;
  }
  .front-brand {
    position: absolute;
    right: 40px;
    top: 46px;
    color: var(--brand-blue);
    font-size: 40px;
    line-height: 1.1;
  }
  .front-brand .brand-name__dot { background: var(--brand-blue); }

  .contact {
    position: absolute;
    right: 34px;
    top: 182px;
    text-align: right;
    color: var(--card-white);
  }
  .contact__name {
    font-size: 22px;
    font-weight: 700;
    margin: 0;
    line-height: 1.1;
  }
  .contact__role {
    font-size: 13px;
    font-weight: 300;
    margin: 2px 0 14px;
  }
  .contact__line {
    display: flex;
    justify-content: flex-end;
    align-items: center;
    gap: 8px;
    font-size: 13px;
    font-weight: 300;
    margin: 0 0 6px;
  }
  .contact__line svg {
    width: 12px;
    height: 12px;
    fill: var(--card-white);
    flex: none;
  }
</style>
</head>
<body>
<main class="canvas">

  <section class="card card--back" aria-label="Business card, back">
    <div class="brand-name">
      <span class="brand-name__dot"></span>
      <span>BrivoTerna</span>
    </div>
  </section>

  <section class="card card--front" aria-label="Business card, front">
    <svg class="front-wave" viewBox="0 0 600 345" preserveAspectRatio="none" aria-hidden="true">
      <path d="M0,345 L0,300 C120,335 200,330 250,280 C320,200 380,130 600,110 L600,345 Z" fill="var(--brand-blue)"/>
    </svg>

    <div class="brand-name front-brand">
      <span class="brand-name__dot"></span>
      <span>BrivoTerna</span>
    </div>

    <div class="contact">
      <p class="contact__name">Teodoro Vinsquel</p>
      <p class="contact__role">CEO &amp; Founder</p>
      <p class="contact__line">+34 655.803.912
        <svg viewBox="0 0 24 24" aria-hidden="true"><path d="M6.6 10.8a15.1 15.1 0 0 0 6.6 6.6l2.2-2.2a1 1 0 0 1 1-.25 11.4 11.4 0 0 0 3.6.57 1 1 0 0 1 1 1V20a1 1 0 0 1-1 1A17 17 0 0 1 3 4a1 1 0 0 1 1-1h3.5a1 1 0 0 1 1 1c0 1.25.2 2.45.57 3.6a1 1 0 0 1-.25 1z"/></svg>
      </p>
      <p class="contact__line">www.brivoterna-example.com
        <svg viewBox="0 0 24 24" aria-hidden="true"><path d="M12 2a10 10 0 1 0 0 20 10 10 0 0 0 0-20zm0 2c.9 0 2.2 1.9 2.8 5H9.2C9.8 5.9 11.1 4 12 4zM4.3 11h3.8a16 16 0 0 0 0 2H4.3a8 8 0 0 1 0-2zm5.9 0h3.6a14 14 0 0 1 0 2h-3.6a14 14 0 0 1 0-2zm5.7 0h3.8a8 8 0 0 1 0 2h-3.8a16 16 0 0 0 0-2zM12 20c-.9 0-2.2-1.9-2.8-5h5.6c-.6 3.1-1.9 5-2.8 5z"/></svg>
      </p>
      <p class="contact__line">teodoro.vinsquel@brivoterna-example.com
        <svg viewBox="0 0 24 24" aria-hidden="true"><path d="M2 5h20v14H2zm2 2v.5l8 5 8-5V7zm0 2.8V17h16V9.8l-8 5z"/></svg>
      </p>
    </div>
  </section>

</main>
</body>
</html>
```